Social Media App Needs PPT Template

We need a PowerPoint template for a new social media company based in the DC area called "Bold Ledger." We provide an interactive digital platform for executives to share actionable advice. We would like to see designs that use our orange logo color as an accent, but are mainly grey, white, and black. The final design should communicate clean, chic, modern, and professional.

Target Market(s)

Executives

Industry/Entity Type

Information Technology

Font styles to use
Sans Serif

Colors
f78f20
fbe7d2
ffffff
000000
e8e8e8
757575

Requirements
Must have
• My project must have title page and many options for the body of the ppt (graphs, tables, etc). It also needs to be easy to modify. I must have someone who is experienced in creating powerpoint templates.
Nice to have
• It would be nice to have a very modern and clean design that includes the logo on every page, but still leaves a lot of room for the content of the slide
Should not have
• My design project should not look to busy.

```html
<!DOCTYPE html>
<html lang="en">
<head>
<meta charset="utf-8">
<title>Bold Ledger – About Our Company</title>
<link href="https://fonts.googleapis.com/css2?family=Lato:wght@300;400&display=swap" rel="stylesheet">
<style>
  :root {
    --orange: #f78f20;
    --orange-deep: #e6821b;
    --black: #000000;
    --white: #ffffff;
    --grey-light: #e8e8e8;
    --grey-mid: #a3a4a7;
    --grey-text: #757575;
    --body-text: #555555;
    --backdrop: #929292;
  }
  * { margin: 0; padding: 0; box-sizing: border-box; }
  html, body {
    width: 1200px; height: 960px; overflow: hidden;
    background: var(--backdrop);
    font-family: 'Lato', sans-serif;
  }
  .slide {
    position: absolute; left: 0; top: 30px;
    width: 1328px; height: 996px;
    transform: scale(0.90361); transform-origin: top left;
    background: radial-gradient(ellipse at 55% 30%, var(--white) 0%, #f4f4f4 60%, #eeeeee 100%);
    overflow: hidden;
  }
  .slide-shapes { position: absolute; left: 0; top: 0; }
  .slide-title {
    position: absolute; left: 40px; top: 86px;
    font-weight: 300; font-size: 52px; color: var(--white); letter-spacing: 0.2px;
  }
  .brand {
    position: absolute; left: 1078px; top: 95px;
    display: flex; align-items: center; gap: 12px;
    color: var(--white); font-size: 30px; font-weight: 400;
  }
  .brand-dot { width: 26px; height: 26px; border-radius: 50%; background: var(--orange); }
  .axis-label {
    position: absolute; width: 30px; text-align: right;
    font-size: 21px; color: var(--grey-text);
  }
  .category-label {
    position: absolute; top: 618px;
    font-size: 22px; color: var(--grey-text);
  }
  .legend { position: absolute; left: 1170px; top: 290px; list-style: none; }
  .legend li {
    display: flex; align-items: center; gap: 6px;
    font-size: 22px; color: var(--grey-text); height: 33px;
  }
  .legend .swatch { width: 13px; height: 13px; }
  .body-copy {
    position: absolute; left: 67px; top: 694px; width: 1201px;
    font-size: 23px; line-height: 34px; color: var(--body-text);
    text-align: justify;
  }
  .footer-text {
    position: absolute; left: 36px; top: 950px;
    font-size: 18px; color: var(--white);
  }
</style>
</head>
<body>
<div class="slide">
  <svg class="slide-shapes" width="1328" height="996" viewBox="0 0 1328 996">
    <!-- header -->
    <polygon points="1032,43 1328,43 1328,57 1018,57" fill="var(--orange-deep)"/>
    <polygon points="0,62 1010,62 900,167 0,167" fill="var(--orange-deep)"/>
    <polygon points="800,62 1010,62 940,130 720,145" fill="var(--orange)" opacity="0.55"/>
    <polygon points="1020,62 1328,62 1328,167 908,167" fill="var(--black)"/>
    <polygon points="0,173 895,173 883,185 0,185" fill="var(--black)"/>
    <!-- chart grid -->
    <g stroke="#999" stroke-width="1.2" stroke-dasharray="9 7">
      <line x1="108" y1="295" x2="1130" y2="295"/>
      <line x1="108" y1="356" x2="1130" y2="356"/>
      <line x1="108" y1="416" x2="1130" y2="416"/>
      <line x1="108" y1="477" x2="1130" y2="477"/>
      <line x1="108" y1="537" x2="1130" y2="537"/>
    </g>
    <line x1="108" y1="295" x2="108" y2="598" stroke="#999" stroke-width="1.2"/>
    <!-- chart areas -->
    <polygon points="485,387 520,378 1130,320 1130,417 1012,438 835,417 500,392" fill="var(--black)"/>
    <polygon points="108,495 343,375 500,392 835,417 1012,438 835,470 500,428 345,455" fill="var(--orange)"/>
    <polygon points="108,495 345,455 500,428 835,470 1012,438 1130,417 1130,598 108,598" fill="var(--grey-mid)"/>
    <line x1="100" y1="598" x2="1130" y2="598" stroke="#999" stroke-width="1.2"/>
    <!-- footer -->
    <polygon points="0,942 380,942 340,982 0,982" fill="var(--black)"/>
    <polygon points="386,942 1328,942 1328,982 346,982" fill="var(--orange-deep)"/>
  </svg>

  <h1 class="slide-title">About Our Company</h1>
  <div class="brand"><span class="brand-dot"></span><span>Bold Ledger</span></div>

  <span class="axis-label" style="left:60px;top:286px">5</span>
  <span class="axis-label" style="left:60px;top:348px">4</span>
  <span class="axis-label" style="left:60px;top:406px">3</span>
  <span class="axis-label" style="left:60px;top:467px">2</span>
  <span class="axis-label" style="left:60px;top:526px">1</span>
  <span class="axis-label" style="left:60px;top:588px">0</span>

  <span class="category-label" style="left:108px">Category 1</span>
  <span class="category-label" style="left:542px">Category 2</span>
  <span class="category-label" style="left:999px">Category 3</span>

  <ul class="legend">
    <li><span class="swatch" style="background:var(--grey-mid)"></span>Series 1</li>
    <li><span class="swatch" style="background:var(--orange)"></span>Series 2</li>
    <li><span class="swatch" style="background:var(--black)"></span>Series 3</li>
  </ul>

  <p class="body-copy">Duis autem vel eum iriure dolor in hendrerit in vulputate velit esse molestie consequat, vel illum dolore eu feugiat nulla facilisis at vero eros et accumsan et iusto odio dignissim qui blandit praesent luptatum zzril delenit augue duis dolore te feugait nulla facilisi. Nam liber tempor cum soluta nobis eleifend option congue nihil imperdiet doming id quod mazim placerat facer possim assum.</p>

  <div class="footer-text">www.boldledger.com &nbsp;|&nbsp; Page 5</div>
</div>
</body>
</html>
```